Business Card Design Project

Business Card design based on logo.
Updates

I need business card, letterhead, envelope, and if possible, Powerpoint slide template.

On front of business card: Just logo- and  my name and title:  Harriet Lindqvist, Principal

On reverse-logo and the rest of the contact info:

4871 Quarry Lane
Davis, CA 95618
650-318-2764
hl@brackenstudyworks.example

On letterhead-Just logo at top, at bottom  the rest-very small along the bottom

On PPT slide-just the logo.

I also want to try a few other colors-I like lime/dark grey (not black) but would like to try Sienna, maybe also indigo or bright blue-green.

I forgot to add-

On the business card-switch to vertical on reverse side and put:

Reverse side-switch to vertical and list:

Harriet Lindqvist
Principal
Bracken Study Works, LLC

650-318-2764

4871 Quarry Lane
Davis, CA 95618

Harriet Lindqvist
Principal

650-318-2764

4871 Quarry Lane
Davis, CA 95618

I have another project at the same time-for Stationery. Feel free to submit to that one also.

That one includes letterhead, envelope, PPT slide, folder cover sheet-HL

Industry/Entity Type

Business

Requirements
Must have
• Must use logo-preferably lime green version-with gray, not black or just 2-tone -logo on colored background.

```html
<!DOCTYPE html>
<html lang="en">
<head>
<meta charset="utf-8">
<title>Bracken Study Works — Business Card</title>
<link href="https://fonts.googleapis.com/css2?family=Source+Sans+3:wght@400;600&display=swap" rel="stylesheet">
<style>
  :root {
    --backdrop: #2a2a2a;
    --card: #ffffff;
    --lime: #8dbb2c;
    --grey: #4a4a4a;
    --text: #333333;
    --rule: #9a9a9a;
  }
  * { box-sizing: border-box; margin: 0; padding: 0; }
  html, body {
    width: 1200px; height: 722px; overflow: hidden;
    background: var(--backdrop);
    font-family: "Source Sans 3", Arial, sans-serif;
  }
  .canvas { position: relative; width: 1200px; height: 722px; }
  .card {
    position: absolute;
    background: var(--card);
    border-radius: 14px;
  }
  .card--front { left: 60px; top: 210px; width: 525px; height: 300px; }
  .card--back  { left: 613px; top: 211px; width: 526px; height: 302px; }

  .brand {
    position: absolute; left: 0; right: 0;
    display: flex; align-items: center; justify-content: center; gap: 12px;
  }
  .card--front .brand { top: 100px; }
  .card--back .brand  { top: 92px; }
  .brand__square { width: 18px; height: 18px; background: var(--lime); }
  .brand__name {
    font-weight: 600; font-size: 26px; letter-spacing: 3px;
    text-transform: uppercase; color: var(--grey);
  }

  .holder {
    position: absolute; left: 0; right: 0; top: 214px;
    text-align: center; font-size: 14px; color: var(--text);
  }
  .holder__name { font-weight: 600; font-size: 16px; color: var(--lime); }

  .company {
    position: absolute; right: 278px; top: 216px;
    text-align: right; color: var(--text);
  }
  .company__name {
    font-weight: 600; font-size: 16px; line-height: 21px; color: var(--lime);
  }
  .company__address { font-size: 13px; margin-top: 7px; white-space: nowrap; }

  .divider {
    position: absolute; left: 262px; top: 219px;
    width: 1px; height: 58px; background: var(--rule);
  }

  .contact {
    position: absolute; left: 274px; top: 216px;
    list-style: none; font-size: 13px; color: var(--text);
  }
  .contact li { display: flex; align-items: center; gap: 8px; height: 21.5px; }
  .contact svg { width: 11px; height: 11px; flex: none; }
</style>
</head>
<body>
<main class="canvas">

  <section class="card card--front" aria-label="Business card front">
    <div class="brand">
      <span class="brand__square"></span>
      <span class="brand__name">Bracken Study Works</span>
    </div>
    <p class="holder"><span class="holder__name">Harriet Lindqvist,</span> Principal</p>
  </section>

  <section class="card card--back" aria-label="Business card back">
    <div class="brand">
      <span class="brand__square"></span>
      <span class="brand__name">Bracken Study Works</span>
    </div>

    <div class="company">
      <p class="company__name">Bracken<br>Study Works, LLC</p>
      <p class="company__address">4871 Quarry Lane Davis, CA 95618</p>
    </div>

    <span class="divider"></span>

    <ul class="contact">
      <li>
        <svg viewBox="0 0 12 12" aria-hidden="true"><path d="M2.5 1 4.5 3.2 3.4 4.6c.7 1.6 2.2 3.1 3.9 3.9l1.3-1.1L11 9.3 9.6 11C5.2 10.6 1.3 6.8 1 2.4Z" fill="var(--lime)"/></svg>
        650-318-2764
      </li>
      <li>
        <svg viewBox="0 0 12 12" aria-hidden="true"><rect x="1" y="2.5" width="10" height="7" fill="var(--lime)"/><path d="M1 2.5 6 6.5 11 2.5" fill="none" stroke="#fff" stroke-width="1"/></svg>
        hl@brackenstudyworks.example
      </li>
      <li>
        <svg viewBox="0 0 12 12" aria-hidden="true"><g fill="none" stroke="var(--lime)" stroke-width="1.1"><circle cx="6" cy="6" r="5"/><ellipse cx="6" cy="6" rx="2.2" ry="5"/><path d="M1 6h10"/></g></svg>
        www.brackenstudyworks.example
      </li>
    </ul>
  </section>

</main>
</body>
</html>
```